Vintage poster/postcard for 2011 New Years Eve event with theme 'Nouveau Cirque'

I have had a major change of mind since the last brief due to my original requirements being too specific. I hope this new brief allows more scope for the designers and I am extending the deadline by 7 days.

For the first time my new business 'Quillmere Gala' is planning an exciting, large scale New Years Eve fundraising event in Hobart Tasmania, Australia. The unique and eclectic theme of the party is 'Nouveau Cirque' (french for contemporary circus). I require a vintage style poster design (similar to a traditional french advertising poster) that can double as a postcard invitation so it must look good on a smaller scale as well.
Updates

Project Deadline Extended
Reason: My original brief was very specific and I now realise very limiting for the designers. I have changed my mind with the look I want for the vintage poster (more along the lines of the traditional french advertising posters of old) and therefore would like to allow designers extra time to submit a design. Thank you. Jun Okafor Quillmere Gala

Target Market(s)

25-50 yr old professionals prepared to pay premium price for a quality, fresh & fun NYE experience while giving to charity.

Industry/Entity Type

Advertising

Requirements
Must have
• - A heading that reads: Quillmere Gala proudly presents
Nouveau Cirque
- Text that includes: 2011 New Years Eve Extravanaganza Saturday 31st December and find out more at "www.quillmeregala-example.com
- A strip left blank at the bottom to include my business logo and others sponsors
- Classic french vintage poster design
- - Plenty of colour but not too fluro
- Something that looks good enough to be framed or sent to a friend
Should not have
• - Picture of Eiffel Tower or any other specific French references
- Any animals

```html
<!DOCTYPE html>
<html lang="en">
<head>
<meta charset="utf-8">
<title>Quillmere Gala – Nouveau Cirque</title>
<link rel="stylesheet" href="https://fonts.googleapis.com/css2?family=Cinzel:wght@600;700;900&family=Rye&display=swap">
<style>
  :root {
    --paper-light: #e6cf9a;
    --paper-dark: #a87f45;
    --ornament-gold: #b88a45;
    --ornament-brown: #5a3a1e;
    --panel-red: #8e2c1f;
    --panel-red-dark: #5e1912;
    --curtain-red: #6f1b14;
    --curtain-deep: #3c0d09;
    --plaque: #2a1a10;
    --cream: #f3e2b8;
    --ink: #2a140b;
    --strip: #0d0907;
  }
  * { margin: 0; padding: 0; box-sizing: border-box; }
  html, body { width: 849px; height: 1200px; overflow: hidden; background: #ffffff; }
  .poster {
    position: relative;
    width: 849px;
    height: 1200px;
    overflow: hidden;
    background: radial-gradient(ellipse at 50% 45%, var(--paper-light) 0%, #cfae6d 60%, var(--paper-dark) 100%);
  }
  .frame-ornament {
    position: absolute;
    inset: 18px;
    border-radius: 14px;
    background: linear-gradient(180deg, #c79d58 0%, var(--ornament-gold) 40%, #8d6030 100%);
    opacity: 0.55;
  }
  .stage-panel {
    position: absolute;
    left: 62px;
    top: 88px;
    width: 725px;
    height: 1040px;
    border-radius: 340px 340px 20px 20px;
    background: radial-gradient(ellipse at 50% 40%, var(--panel-red) 0%, var(--panel-red-dark) 100%);
    border: 6px solid var(--ornament-brown);
    box-shadow: inset 0 0 0 4px var(--ornament-gold);
  }
  .curtain {
    position: absolute;
    left: 262px;
    top: 640px;
    width: 325px;
    height: 488px;
    border-radius: 160px 160px 0 0;
    background: linear-gradient(90deg, var(--curtain-deep) 0%, var(--curtain-red) 30%, #8a2a1c 50%, var(--curtain-red) 70%, var(--curtain-deep) 100%);
  }
  .presenter-plaque {
    position: absolute;
    left: 170px;
    top: 132px;
    width: 509px;
    height: 150px;
    border-radius: 75px;
    background: var(--plaque);
    border: 5px solid var(--ornament-gold);
    box-shadow: 0 0 0 3px var(--ornament-brown);
    display: flex;
    flex-direction: column;
    align-items: center;
    justify-content: center;
    color: var(--cream);
    font-family: "Cinzel", serif;
    text-align: center;
  }
  .presenter-name { font-size: 54px; font-weight: 900; line-height: 1; letter-spacing: 1px; }
  .presenter-tag { font-size: 32px; font-weight: 700; line-height: 1.2; margin-top: 4px; }
  .event-title {
    position: absolute;
    left: 0;
    width: 849px;
    text-align: center;
    font-family: "Rye", serif;
    color: var(--cream);
    -webkit-text-stroke: 3px var(--ink);
    paint-order: stroke fill;
    text-shadow: 4px 4px 0 var(--ink);
    line-height: 1;
  }
  .title-line-1 { top: 305px; font-size: 128px; letter-spacing: 2px; }
  .title-line-2 { top: 432px; font-size: 128px; letter-spacing: 4px; }
  .event-subtitle {
    position: absolute;
    left: 0;
    width: 849px;
    text-align: center;
    font-family: "Cinzel", serif;
    font-weight: 900;
    color: var(--cream);
    text-shadow: 3px 3px 0 var(--ink);
    line-height: 1;
  }
  .subtitle-line-1 { top: 590px; font-size: 54px; }
  .subtitle-line-2 { top: 652px; font-size: 60px; letter-spacing: 2px; }
  .event-date {
    position: absolute;
    top: 985px;
    left: 0;
    width: 849px;
    text-align: center;
    font-family: "Cinzel", serif;
    font-weight: 900;
    font-size: 40px;
    color: var(--cream);
    text-shadow: 2px 2px 0 var(--ink);
  }
  .event-web {
    position: absolute;
    top: 1040px;
    left: 0;
    width: 849px;
    text-align: center;
    font-family: "Cinzel", serif;
    font-weight: 600;
    font-size: 22px;
    color: var(--cream);
  }
  .sponsor-strip {
    position: absolute;
    left: 210px;
    top: 1075px;
    width: 570px;
    height: 50px;
    border-radius: 25px;
    background: var(--strip);
  }
</style>
</head>
<body>
  <main class="poster">
    <div class="frame-ornament" role="img" aria-label="Ornate art nouveau scrollwork border in gold and brown"></div>
    <div class="stage-panel"></div>
    <div class="curtain" role="img" aria-label="Illustration of draped red circus tent curtains"></div>

    <header class="presenter-plaque">
      <div class="presenter-name">QUILLMERE GALA</div>
      <div class="presenter-tag">PROUDLY PRESENTS</div>
    </header>

    <h1>
      <span class="event-title title-line-1">NOUVEAU</span>
      <span class="event-title title-line-2">CIRQUE</span>
    </h1>

    <p class="event-subtitle subtitle-line-1">2011 NEW YEARS EVE</p>
    <p class="event-subtitle subtitle-line-2">EXTRAVAGANZA</p>

    <p class="event-date">SATURDAY 31ST DECEMBER</p>
    <p class="event-web">WWW.QUILLMEREGALA-EXAMPLE.COM</p>

    <div class="sponsor-strip" aria-label="Space reserved for sponsor logos"></div>
  </main>
</body>
</html>
```